Luxury Wine Label for New Startup Winery

We need a wine label for our new winery startup. We have worked with a local designer but do not feel the resulting label / logo have the elevation required to present our brand as a luxury wine. Our winery is called "Quailbrook Vineyards" and we are focused on extremely high quality hand crafted artisan and estate wines from the Pacific Northwest.
We would like to see designs that utilize a tree line, or other imagery that represents the "Quailbrook" part of our company name. Another interesting feature could be wood grain.
A logo will be required based on your design so please design with this in mind:
This logo should be consistent with the wine bottle label design, and should be representative of our high end exclusive wine while giving a sense of place (Oregon/ Pacific Northwest.)
I will supply an image of the design we received from our local designer, PLEASE NOTE: in general we do like wood grain and tree line concepts but feel the execution was poorly done.
ATTN: Logo design should be suitable for use on: Bottles (Red wine/rose/white wine), Bussiness cards, vehicle signage, business signage, etc
P.S.:
If you have a design that is not outside the box we are still interested in seeing it.
Label is for a burgundy style bottle with a label height of 3.5 - 4" and a width of 3.5-4"
any label <= 4"x4" and >=3.5"x3.5" will be acceptable:
HOWEVER Width should be greater than or equal to height due to the bottle format
Target Market(s)
Wine enthusiasts with adequate discretionary budgets to afford $100 bottles of wine.
Industry/Entity Type
Wine / Winery
Requirements
Must have
- A sense of luxury, a feel of exclusivity, and a theme consistent with our product and brand name
Nice to have
- Tree line, wood grain or other wood themes. Serif fonts
Should not have
- anything cheesy, off topic, hard to read script fonts or anything that makes the label hard to read from a few feet away or too busy

```html
<!DOCTYPE html>
<html lang="en">
<head>
<meta charset="utf-8">
<title>Quailbrook Vineyards – Syrah Label</title>
<link rel="stylesheet" href="https://fonts.googleapis.com/css2?family=Josefin+Sans:wght@300&family=Cinzel:wght@600&family=Montserrat:wght@300&family=Cormorant+Garamond:wght@600&family=Berkshire+Swash&family=Great+Vibes&family=Parisienne&family=Yellowtail&family=Norican&family=Alex+Brush&display=swap">
<style>
  :root {
    --canvas: #ffffff;
    --label-black: #0d0d0d;
    --label-black-edge: #1a1a1a;
    --gold-light: #f3dc85;
    --gold-mid: #c9a13f;
    --gold-deep: #9a6b1f;
    --gold-copper: #c0782a;
    --wood-dark: #2e2016;
    --wood-mid: #4a3523;
    --silver: #d4d4d4;
    --soft-white: #e9e9e9;
    --ink: #111111;
  }
  * { margin: 0; padding: 0; box-sizing: border-box; }
  html, body { width: 1200px; height: 1126px; overflow: hidden; background: var(--canvas); }
  .canvas { position: relative; width: 1200px; height: 1126px; }

  .gold-rule {
    position: absolute; left: 17px; right: 17px;
    background: linear-gradient(90deg, var(--gold-deep), var(--gold-light) 25%, var(--gold-mid) 50%, var(--gold-light) 70%, var(--gold-copper));
  }

  /* Front label */
  .front-label {
    position: absolute; left: 327px; top: 69px; width: 545px; height: 475px;
    background: linear-gradient(180deg, var(--label-black-edge), var(--label-black) 50%, var(--label-black-edge));
  }
  .front-label .rule-top { top: 6px; height: 4px; }
  .front-label .rule-band { top: 363px; height: 13px; }
  .brand-name {
    position: absolute; left: 0; right: 0; text-align: center;
    font-family: "Josefin Sans", sans-serif; font-weight: 300;
    color: var(--gold-mid);
  }
  .brand-name .primary { position: absolute; left: 0; right: 0; top: 172px; font-size: 60px; letter-spacing: 3px; }
  .brand-name .secondary { position: absolute; left: 0; right: 0; top: 266px; font-size: 36px; letter-spacing: 6px; }
  .region {
    position: absolute; left: 0; right: 0; top: 408px; text-align: center;
    font-family: "Montserrat", sans-serif; font-weight: 300;
    font-size: 28px; letter-spacing: 1px; color: var(--soft-white);
  }

  /* Varietal strip */
  .varietal-label {
    position: absolute; left: 327px; top: 608px; width: 545px; height: 117px;
    background: linear-gradient(90deg, var(--wood-dark), var(--wood-mid) 30%, var(--wood-dark) 55%, var(--wood-mid) 80%, var(--wood-dark));
  }
  .varietal-label .rule-top { top: 8px; height: 5px; }
  .varietal-label .rule-bottom { top: 105px; height: 6px; }
  .varietal-name {
    position: absolute; left: 0; right: 0; top: 6px; text-align: center;
    font-family: "Berkshire Swash", cursive; font-size: 50px; letter-spacing: 4px; color: var(--silver);
  }
  .vintage-line {
    position: absolute; left: 0; right: 0; top: 66px; text-align: center;
    font-family: "Cormorant Garamond", serif; font-weight: 600;
    font-size: 27px; letter-spacing: 3px; color: var(--soft-white);
  }

  /* Script options */
  .script-options { position: absolute; left: 0; top: 0; width: 1200px; height: 1126px; }
  .script-sample { position: absolute; transform: translate(-50%, -50%); color: var(--ink); white-space: nowrap; }
  .s1 { left: 451px; top: 865px; font-family: "Great Vibes", cursive; font-size: 66px; }
  .s2 { left: 611px; top: 863px; font-family: "Parisienne", cursive; font-size: 46px; }
  .s3 { left: 753px; top: 862px; font-family: "Yellowtail", cursive; font-size: 52px; }
  .s4 { left: 451px; top: 930px; font-family: "Parisienne", cursive; font-size: 44px; }
  .s5 { left: 611px; top: 928px; font-family: "Norican", cursive; font-size: 44px; }
  .s6 { left: 765px; top: 932px; font-family: "Alex Brush", cursive; font-size: 62px; }
</style>
</head>
<body>
<main class="canvas">
  <section class="front-label" role="img" aria-label="Front label on black pinstripe paper">
    <div class="gold-rule rule-top"></div>
    <div class="brand-name">
      <div class="primary">QUAILBROOK</div>
      <div class="secondary">VINEYARDS</div>
    </div>
    <div class="gold-rule rule-band"></div>
    <div class="region">WILLAMETTE VALLEY</div>
  </section>

  <section class="varietal-label" role="img" aria-label="Varietal strip label on dark walnut wood grain">
    <div class="gold-rule rule-top"></div>
    <div class="varietal-name">Syrah</div>
    <div class="vintage-line">ESTATE | 2023 | GROWN</div>
    <div class="gold-rule rule-bottom"></div>
  </section>

  <section class="script-options" aria-label="Script options for the varietal name">
    <span class="script-sample s1">Syrah</span>
    <span class="script-sample s2">Syrah</span>
    <span class="script-sample s3">Syrah</span>
    <span class="script-sample s4">Syrah</span>
    <span class="script-sample s5">Syrah</span>
    <span class="script-sample s6">Syrah</span>
  </section>
</main>
</body>
</html>
```